Creation of an elegant and modern turnkey Shopify website

Hello,

We are a new company specializing in the sale of above-ground pools. We want to create a turnkey website, ideally using Shopify. For now, we need a "showcase" site, not an e-commerce platform, with four tabs:

Home Page (an overall presentation of the company)
Our Products (an overview of all the above-ground pools we sell)
Our Projects (a page inspired by Instagram to showcase photos of our future projects)
Contact (a page with all our contact information and a contact form)

We are looking to create a highly visual, elegant, and modern website with vibrant splashes of color. We will provide the text, photos (along with instructions on where to place them on each page), and all other necessary information as attachments.

Thank you in advance for your proposals!

The Brisa Lagoon Team

Target Market(s)

Targeted at Swiss customers (a translator will need to be installed for different languages)

Industry/Entity Type

Sale of customised above-ground pools

Coding

Coded - Design and coding required

Font styles to use
Sans Serif

Colors
0094D4
00A9DD
6FCCEA
C7EBF8
E9F6FB
00AB8E
00BBA5
67D7C9
C6EFE9
E9F9F6

Requirements
Must have
• A stunning, elegant and modern look
Nice to have
• Inspiration from the colors of our logo throughout the site, but in an elegant way
Should not have
• An overly classic look for swimming pool sites

```html
<!DOCTYPE html>
<html lang="en">
<head>
<meta charset="utf-8">
<title>Brisa Lagoon — Above-Ground Pools</title>
<link href="https://fonts.googleapis.com/css2?family=Italiana&family=Lato:wght@400;700&display=swap" rel="stylesheet">
<style>
:root{
  --deep:#0094D4;
  --sea:#00A9DD;
  --sky:#6FCCEA;
  --mist:#E9F6FB;
  --aqua:#00E1F7;
  --icon:#12C8E6;
  --ink:#111418;
  --text:#2b2f33;
  --line:#cfdce2;
  --night:#1d1d1d;
  --white:#ffffff;
  --display:"Italiana", serif;
  --body:"Lato", sans-serif;
}
*{box-sizing:border-box;margin:0;padding:0}
html,body{width:1200px;height:2843px;overflow:hidden}
body{position:relative;font-family:var(--body);color:var(--text);background:var(--mist)}
.abs{position:absolute}

/* hero */
.hero{left:0;top:0;width:1200px;height:641px;background:radial-gradient(ellipse at 70% 45%,#1fa9d9 0%,#0a86c2 45%,#045f96 100%)}
.hero-photo{left:540px;top:100px;width:480px;height:541px;background:radial-gradient(ellipse at 50% 50%,rgba(240,210,40,.55) 0%,rgba(240,210,40,.25) 40%,rgba(240,210,40,0) 70%)}
.brand{font-family:var(--display);color:var(--white);font-size:40px;line-height:40px;letter-spacing:1px}
.nav{left:494px;top:44px;display:flex;gap:46px;font-family:var(--display);color:var(--white);font-size:24px}
.nav-tools{left:915px;top:45px;display:flex;gap:28px;align-items:center;color:var(--white);font-weight:700;font-size:16px}
.hero h1{left:111px;top:174px;width:560px;font-family:var(--display);font-weight:400;color:var(--white);font-size:39px;line-height:60px}
.hero-lede{left:111px;top:362px;width:380px;color:var(--white);font-weight:700;font-size:15.5px;line-height:29px}
.btn-start{left:111px;top:445px;width:140px;height:47px;background:var(--white);border-radius:5px;font-family:var(--display);font-size:19px;color:var(--ink);display:flex;align-items:center;justify-content:center}
.arrow{width:28px;height:28px;border-radius:50%;background:var(--white);top:326px;display:flex;align-items:center;justify-content:center}

/* sections */
.section-title{left:0;width:1200px;text-align:center;font-family:var(--display);font-weight:400;font-size:38px;color:var(--ink)}
.card{width:294px;height:352px;background:var(--white);border:1px solid var(--line);text-align:center}
.card .badge{position:absolute;left:83px;top:35px;width:128px;height:128px;border-radius:50%;border:1px solid #e3eaee;display:flex;align-items:center;justify-content:center}
.card h3{position:absolute;left:0;top:196px;width:100%;font-family:var(--display);font-weight:400;font-size:22px;color:var(--ink)}
.card p{position:absolute;left:20px;top:238px;width:254px;font-size:13px;line-height:26px;color:var(--text)}

.about{left:0;top:1233px;width:1200px;height:529px;background:linear-gradient(100deg,#4c8fa0 0%,#1b7890 35%,#0f5e77 70%,#0c4e66 100%)}
.about-photo{left:0;top:0;width:520px;height:529px;background:radial-gradient(ellipse at 40% 60%,rgba(40,70,80,.6) 0%,rgba(40,70,80,0) 60%)}
.about h2{position:absolute;left:627px;top:95px;font-family:var(--display);font-weight:400;font-size:38px;color:var(--white)}
.about p{position:absolute;left:627px;top:155px;width:470px;color:var(--white);font-weight:700;font-size:15.5px;line-height:31px}
.watch{position:absolute;left:623px;top:366px;display:flex;align-items:center;gap:20px;font-family:var(--display);font-size:29px;color:var(--white)}
.watch .play{width:56px;height:56px;border-radius:50%;background:rgba(255,255,255,.35);display:flex;align-items:center;justify-content:center}
.watch .play span{width:44px;height:44px;border-radius:50%;background:var(--white);display:flex;align-items:center;justify-content:center}

.banner{left:0;top:2292px;width:1200px;height:108px;background:var(--aqua);display:flex;align-items:center;justify-content:center;font-family:var(--display);font-size:38px;color:var(--ink)}

/* footer */
.footer{left:0;top:2400px;width:1200px;height:443px;background:var(--night);color:#cfcfcf}
.footer .brand{left:111px;top:95px;font-size:48px;line-height:56px}
.foot-address{left:109px;top:250px;font-size:15px;line-height:31px;color:#bdbdbd}
.foot-col h4{font-family:var(--display);font-weight:400;font-size:21px;color:var(--white);margin-bottom:18px}
.foot-col li{list-style:none;font-size:15px;line-height:31px;color:#d2d2d2}
.newsletter{left:805px;top:135px;width:285px;height:43px;border:1px solid #8a8a8a;display:flex;align-items:center;justify-content:space-between;padding:0 24px 0 18px;font-size:11px;color:#9a9a9a}
.newsletter b{font-family:var(--display);font-weight:400;font-size:15px;color:var(--white)}
.copyright{left:110px;top:2762px;font-size:15px;color:#bdbdbd}
</style>
</head>
<body>

<header class="abs hero">
  <div class="abs hero-photo" role="img" aria-label="Photo of a woman floating on a yellow swim ring in bright blue pool water"></div>
  <div class="abs brand" style="left:111px;top:18px">BRISA<br>LAGOON</div>
  <nav class="abs nav"><span>HOME</span><span>ABOUT</span><span>WHY CHOOSE US</span></nav>
  <div class="abs nav-tools">
    <svg width="16" height="16" viewBox="0 0 16 16" fill="none" stroke="#fff" stroke-width="2.4"><circle cx="6.5" cy="6.5" r="4.5"/><path d="M10 10l4 4"/></svg>
    <svg width="16" height="18" viewBox="0 0 16 18" fill="#fff"><circle cx="8" cy="5" r="4.5"/><path d="M0 18c0-5 3.5-7 8-7s8 2 8 7z"/></svg>
    <span style="display:flex;align-items:center;gap:6px">En
      <svg width="24" height="22" viewBox="0 0 24 22" fill="none" stroke="#fff" stroke-width="1.5"><circle cx="10" cy="11" r="9"/><ellipse cx="10" cy="11" rx="4" ry="9"/><path d="M1 11h18M3 6h14M3 16h14"/><path d="M19 14l2.5 2.5L24 14"/></svg>
    </span>
  </div>
  <h1 class="abs">TRANSFORM YOUR GARDEN WITH OUR PREMIUM ABOVEGROUND POOLS</h1>
  <p class="abs hero-lede">Achieve your dreams with our custom, tailor-made above-ground pools.</p>
  <div class="abs btn-start">GET STARTED</div>
  <div class="abs arrow" style="left:41px"><svg width="10" height="12" viewBox="0 0 10 12" fill="none" stroke="#222" stroke-width="2.4"><path d="M7 1L2 6l5 5"/></svg></div>
  <div class="abs arrow" style="left:1121px"><svg width="10" height="12" viewBox="0 0 10 12" fill="none" stroke="#222" stroke-width="2.4"><path d="M3 1l5 5-5 5"/></svg></div>
</header>

<h2 class="abs section-title" style="top:703px">WHY CHOOSE OUR ABOVE GROUND POOLS</h2>

<article class="abs card" style="left:111px;top:799px">
  <div class="badge"><svg width="48" height="48" viewBox="0 0 48 48" fill="none" stroke="var(--icon)" stroke-width="2.4"><circle cx="24" cy="24" r="20"/><circle cx="24" cy="24" r="14"/><path d="M16 28l2-9 6 5 6-5 2 9z"/></svg></div>
  <h3>SUPERIOR QUALITY</h3>
  <p>Each pool is constructed with high-quality materials, ensuring exceptional durability and strength.</p>
</article>
<article class="abs card" style="left:453px;top:799px">
  <div class="badge"><svg width="52" height="48" viewBox="0 0 52 48" fill="none" stroke="var(--icon)" stroke-width="2.6"><path d="M26 6v30M18 14c0 8 4 14 8 22M34 14c0 8-4 14-8 22M8 28c6 0 10 4 12 10M44 28c-6 0-10 4-12 10M10 42h32"/></svg></div>
  <h3>ELEGANT DESIGN</h3>
  <p>Our pools come in a variety of styles and finishes, seamlessly blending into any garden setting.</p>
</article>
<article class="abs card" style="left:794px;top:799px">
  <div class="badge"><svg width="52" height="52" viewBox="0 0 52 52" fill="none" stroke="var(--icon)" stroke-width="2.2"><rect x="12" y="12" width="34" height="34"/><path d="M6 6h24M12 20h34M16 28h10v12H16zM30 28h12M30 34h12M30 40h12"/></svg></div>
  <h3>CUSTOM AND TAILOR MADE</h3>
  <p>Create the pool of your dreams with our customization options, tailored to your specific tastes and needs.</p>
</article>

<section class="abs about">
  <div class="abs about-photo" role="img" aria-label="Photo of a woman in a swimsuit sitting at the edge of a turquoise pool"></div>
  <h2>ABOUT BRISA LAGOON</h2>
  <p>Imagine an exceptional relaxation and leisure space right in your own backyard. With our unparalleled expertise and commitment to excellence, we create above-ground pools that exceed all expectations. Our exclusive, custom-designed models are crafted to combine style, durability, and innovation, offering a unique and refined experience.</p>
  <div class="watch"><div class="play"><span><svg width="16" height="18" viewBox="0 0 16 18" fill="var(--icon)"><path d="M2 1l13 8-13 8z"/></svg></span></div>WATCH VIDEO</div>
</section>

<article class="abs card" style="left:111px;top:1852px">
  <div class="badge"><svg width="52" height="52" viewBox="0 0 52 52" fill="none" stroke="var(--icon)" stroke-width="2.4"><circle cx="26" cy="26" r="14"/><circle cx="26" cy="22" r="5"/><path d="M18 35c2-5 14-5 16 0M8 26a18 18 0 0 1 30-13M44 26a18 18 0 0 1-30 13M38 8v6h-6M14 44v-6h6"/></svg></div>
  <h3>PERSONALIZED SERVICES</h3>
  <p>We understand that every garden and client is unique.</p>
</article>
<article class="abs card" style="left:452px;top:1852px">
  <div class="badge"><svg width="52" height="52" viewBox="0 0 52 52" fill="none" stroke="var(--icon)" stroke-width="2.2"><path d="M12 8l2 4 4 1-3 3 1 4-4-2-4 2 1-4-3-3 4-1zM26 4l2 4 4 1-3 3 1 4-4-2-4 2 1-4-3-3 4-1zM40 8l2 4 4 1-3 3 1 4-4-2-4 2 1-4-3-3 4-1z"/><path d="M12 30h8v18h-8zM20 32l6-10c3 0 4 2 3 6h10c2 0 3 2 2 4l-3 12c-1 2-2 3-4 3H20"/></svg></div>
  <h3>GUARANTEED SATISFACTION</h3>
  <p>Your satisfaction is our top priority. We are committed to providing you with exceptional.</p>
</article>
<article class="abs card" style="left:793px;top:1852px">
  <div class="badge"><svg width="44" height="44" viewBox="0 0 44 44" fill="none" stroke="var(--icon)" stroke-width="2.6"><path d="M10 4l7 8-4 5c3 6 8 11 14 14l5-4 8 7-5 6C20 40 4 24 4 9z"/><path d="M26 4a14 14 0 0 1 14 14M26 11a7 7 0 0 1 7 7"/></svg></div>
  <h3>CONTACT US TODAY</h3>
  <p>Don't wait any longer to transform your garden into a wellness oasis</p>
</article>

<div class="abs banner">WE BRING YOUR POOL DREAMS TO LIFE</div>

<footer class="abs footer">
  <div class="abs brand">BRISA<br>LAGOON</div>
  <p class="abs foot-address">Lucia Moretti, Rue des<br>Tilleuls 27, 1400 Yverdon<br>079 000 12 34</p>
  <div class="abs foot-col" style="left:381px;top:92px">
    <h4>ABOUT BRISA</h4>
    <ul><li>About us</li><li>About</li><li>Why Choose Us</li><li>Contact us</li><li>Faq's</li></ul>
  </div>
  <div class="abs foot-col" style="left:600px;top:92px">
    <h4>SUPPORT</h4>
    <ul><li>Privacy policy</li><li>Return policy</li><li>Terms &amp; condition</li><li>Contact us</li></ul>
  </div>
  <div class="abs foot-col" style="left:806px;top:92px"><h4>JOIN OUR NEWSLETTER</h4></div>
  <div class="abs newsletter"><span>@email.com</span><b>SUBMIT</b></div>
</footer>
<p class="abs copyright">Copyrights@2024.Brisa Lagoon.All Rights Reserved</p>

</body>
</html>
```